Email Signature Block Design for Law Firm

I would like you to create a similar signature block for my law firm . I saw the email signature block attached as image002.png and wanted a similar design for my law firm. I want to be able to swap the portraits for each of my staff from the final design. Our law firm colors are black, gold, white, red.

Industry/Entity Type

Law

Requirements
Nice to have
• i like the red circle in around the photo in the tall oak group design. The Silver Lark Co desgn is what inspired me to have a signature block design for my firm.

```html
<!DOCTYPE html>
<html lang="en">
<head>
<meta charset="UTF-8">
<title>The Harlow Firm – Email Signature</title>
<link href="https://fonts.googleapis.com/css2?family=Cinzel:wght@400;500&family=Marcellus&family=Montserrat:wght@400&display=swap" rel="stylesheet">
<style>
  :root {
    --gold: #c9972e;
    --red: #d71f26;
    --black: #0a0a0a;
    --white: #ffffff;
    --ink: #3a3a3a;
    --grey: #9a9a9a;
    --badge-blue: #8fcbe0;
    --badge-slate: #dfe4ea;
    --badge-dark: #2b2b2b;
  }
  html, body {
    margin: 0;
    padding: 0;
    width: 1200px;
    height: 400px;
    overflow: hidden;
    background: var(--white);
  }
  .signature {
    position: relative;
    width: 1200px;
    height: 400px;
    overflow: hidden;
    background: var(--white);
  }
  .firm-lockup {
    position: absolute;
    left: 40px;
    top: 38px;
    display: flex;
    align-items: center;
    gap: 14px;
  }
  .firm-lockup__square {
    width: 44px;
    height: 44px;
    background: var(--gold);
  }
  .firm-lockup__text {
    display: flex;
    flex-direction: column;
  }
  .firm-lockup__name {
    font-family: "Cinzel", serif;
    font-weight: 500;
    font-size: 20px;
    color: var(--ink);
    letter-spacing: 0.5px;
    line-height: 1;
  }
  .firm-lockup__tagline {
    display: flex;
    align-items: center;
    gap: 6px;
    margin-top: 5px;
    font-family: "Marcellus", serif;
    font-size: 9px;
    letter-spacing: 2.6px;
    color: var(--ink);
  }
  .firm-lockup__rule {
    flex: 1;
    height: 1px;
    background: var(--ink);
  }
  .person {
    position: absolute;
    left: 42px;
    top: 164px;
  }
  .person__name {
    margin: 0;
    font-family: "Cinzel", serif;
    font-weight: 400;
    font-size: 40px;
    line-height: 1;
    color: var(--gold);
    letter-spacing: 0.5px;
  }
  .person__title {
    margin: 10px 0 0 1px;
    font-family: "Montserrat", sans-serif;
    font-size: 16px;
    letter-spacing: 2.5px;
    color: var(--grey);
  }
  .contact-band {
    position: absolute;
    left: 0;
    top: 304px;
    width: 1200px;
    height: 96px;
    background: var(--black);
  }
  .contact-list {
    position: absolute;
    margin: 0;
    padding: 0;
    list-style: none;
    font-family: "Marcellus", serif;
    font-size: 21px;
    color: var(--white);
  }
  .contact-list li {
    display: flex;
    align-items: center;
    height: 27px;
  }
  .contact-list--left {
    left: 42px;
    top: 321px;
  }
  .contact-list--left svg {
    width: 14px;
    height: 14px;
    margin-right: 12px;
  }
  .contact-list--right {
    right: 43px;
    top: 321px;
    text-align: right;
  }
  .contact-list--right li {
    justify-content: flex-end;
  }
  .contact-list--right svg {
    width: 13px;
    height: 14px;
    margin-left: 12px;
  }
  .portrait {
    position: absolute;
    left: 460px;
    top: 60px;
    width: 316px;
    height: 316px;
  }
  .awards {
    position: absolute;
    right: 0;
    top: 0;
    width: 160px;
    height: 300px;
  }
</style>
</head>
<body>
  <div class="signature">

    <div class="firm-lockup">
      <div class="firm-lockup__square"></div>
      <div class="firm-lockup__text">
        <span class="firm-lockup__name">The Harlow Firm, PLLC</span>
        <span class="firm-lockup__tagline">
          <span class="firm-lockup__rule"></span>Attorneys At Law<span class="firm-lockup__rule"></span>
        </span>
      </div>
    </div>

    <div class="person">
      <h1 class="person__name">Name Surname</h1>
      <p class="person__title">TITLE</p>
    </div>

    <div class="contact-band"></div>

    <svg class="portrait" viewBox="0 0 316 316">
      <defs>
        <linearGradient id="portrait-fill" x1="0" y1="0" x2="0" y2="1">
          <stop offset="0" stop-color="#f2f2f2"/>
          <stop offset="0.55" stop-color="#8a6a5a"/>
          <stop offset="1" stop-color="#1f2330"/>
        </linearGradient>
      </defs>
      <circle cx="158" cy="158" r="148" fill="var(--white)"/>
      <circle cx="158" cy="158" r="139" fill="url(#portrait-fill)" role="img" aria-label="Staff portrait photo: smiling attorney in dark suit and blue striped tie"/>
      <circle cx="158" cy="158" r="148" fill="none" stroke="var(--red)" stroke-width="19"/>
    </svg>

    <svg class="awards" viewBox="0 0 160 300">
      <rect x="20" y="28" width="114" height="36" rx="3" fill="var(--badge-blue)" role="img" aria-label="Local readers' choice award badge"/>
      <rect x="20" y="80" width="108" height="70" rx="3" fill="var(--badge-slate)" role="img" aria-label="Lawyer recognition listing badge"/>
      <circle cx="74" cy="216" r="55" fill="var(--badge-dark)" role="img" aria-label="Regional best-of award seal"/>
    </svg>

    <ul class="contact-list contact-list--left">
      <li>
        <svg viewBox="0 0 24 24"><path fill="var(--red)" d="M6.6 10.8c1.4 2.8 3.8 5.1 6.6 6.6l2.2-2.2c.3-.3.7-.4 1-.2 1.1.4 2.3.6 3.6.6.6 0 1 .4 1 1V20c0 .6-.4 1-1 1C10.6 21 3 13.4 3 4c0-.6.4-1 1-1h3.5c.6 0 1 .4 1 1 0 1.3.2 2.5.6 3.6.1.3 0 .7-.2 1z"/></svg>
        555-018-4462
      </li>
      <li>
        <svg viewBox="0 0 24 24"><path fill="var(--red)" d="M2 5h20v14H2z"/><path fill="none" stroke="var(--black)" stroke-width="1.8" d="M2 5l10 8 10-8"/></svg>
        contact@harlow-firm.com
      </li>
    </ul>

    <ul class="contact-list contact-list--right">
      <li>
        harlowfirmlaw
        <svg viewBox="0 0 24 24"><rect x="4" y="4" width="16" height="16" rx="4" fill="none" stroke="var(--red)" stroke-width="2.4"/></svg>
      </li>
      <li>
        Bayport, FL
        <svg viewBox="0 0 24 24"><path fill="var(--red)" d="M12 2C8.1 2 5 5.1 5 9c0 5.2 7 13 7 13s7-7.8 7-13c0-3.9-3.1-7-7-7zm0 9.5c-1.4 0-2.5-1.1-2.5-2.5S10.6 6.5 12 6.5s2.5 1.1 2.5 2.5-1.1 2.5-2.5 2.5z"/></svg>
      </li>
    </ul>

  </div>
</body>
</html>
```